Woman owned consulting company needs an elegant and modern business card design

I need a business card design for my new consulting company, Mara Quillon Consulting. I am looking for something that is simple and elegant, but also creative and original. You can use either version of the logo that are attached. I have also included the information that needs to be featured on the business card.

Contact Information for Business Card

Requirements
Must have
• The logo and the font type and a standard business card size. Use shades of gray/silver and or rose gold that are in the logo.
• I didn't realize that my actual logo wasn't attached. Please incorporate in the designs.
Should not have
• Colors that are different from my logo

```html
<!DOCTYPE html>
<html lang="en">
<head>
<meta charset="utf-8">
<title>Mara Quillon Consulting – Business Card</title>
<link href="https://fonts.googleapis.com/css2?family=Cinzel:wght@400;600&family=Lora:wght@400&display=swap" rel="stylesheet">
<style>
  :root {
    --backdrop: #c9c9c9;
    --charcoal: #3a3f42;
    --paper: #f4f4f3;
    --silver: #a3a3a3;
    --silver-light: #d9d9d9;
    --ink: #2b2b2b;
    --edge: #c4c4c4;
    --white: #ffffff;
  }
  * { margin: 0; padding: 0; box-sizing: border-box; }
  html, body { width: 1200px; height: 852px; overflow: hidden; }
  body {
    background: var(--backdrop);
    position: relative;
    font-family: "Lora", Georgia, serif;
  }
  .card {
    position: absolute;
    top: 272px;
    width: 540px;
    height: 309px;
    border-radius: 16px;
    overflow: hidden;
  }
  .card--front { left: 40px; background: var(--charcoal); }
  .card--back { left: 620px; background: var(--paper); }

  .brand {
    position: absolute;
    font-family: "Cinzel", Georgia, serif;
    font-weight: 400;
    line-height: 1.05;
    letter-spacing: 1px;
    display: flex;
    align-items: center;
    gap: 14px;
  }
  .brand__dot {
    width: 12px; height: 12px; border-radius: 50%;
    flex: none;
  }
  .card--front .brand {
    left: 0; right: 0; top: 120px;
    justify-content: center;
    color: var(--silver-light);
    font-size: 28px;
  }
  .card--front .brand__dot { background: var(--silver-light); }
  .card--back .brand {
    left: 48px; top: 40px;
    color: var(--silver);
    font-size: 27px;
  }
  .card--back .brand__dot { background: var(--silver); }

  .person { position: absolute; left: 44px; top: 188px; color: var(--ink); }
  .person__name {
    font-family: "Cinzel", Georgia, serif;
    font-weight: 600;
    font-size: 21px;
    letter-spacing: 1px;
  }
  .person__role { font-size: 13px; margin-top: 2px; }

  .contacts {
    position: absolute; left: 280px; top: 118px;
    list-style: none; color: var(--ink); font-size: 12px;
  }
  .contacts li { display: flex; align-items: center; gap: 10px; height: 19px; }
  .contacts svg { width: 11px; height: 11px; fill: var(--ink); flex: none; }

  .footer-band { position: absolute; left: 0; bottom: 0; width: 540px; height: 80px; }
  .footer-tab {
    position: absolute; left: 244px; right: 0; bottom: 0; height: 68px;
    display: flex; align-items: center; justify-content: center;
    padding: 0 14px 6px;
  }
  .footer-tab__label {
    font-family: "Cinzel", Georgia, serif;
    font-size: 13px; letter-spacing: 0.3px;
    color: var(--white);
    white-space: nowrap;
  }
</style>
</head>
<body>

<section class="card card--front">
  <div class="brand"><span class="brand__dot"></span><span>Mara Quillon<br>Consulting, LLC</span></div>
</section>

<section class="card card--back">
  <div class="brand"><span class="brand__dot"></span><span>Mara Quillon<br>Consulting, LLC</span></div>

  <ul class="contacts">
    <li>
      <svg viewBox="0 0 12 12"><path d="M1 4c0-2 2-3 5-3s5 1 5 3v1H8V4H4v1H1zM3 6h6l1.5 5h-9z"/></svg>
      555-014-8827
    </li>
    <li>
      <svg viewBox="0 0 12 12"><path d="M0 2h12v8H0zM1 3v.3l5 3.4 5-3.4V3z" fill-rule="evenodd"/></svg>
      mara@maraquillonconsulting.com
    </li>
    <li>
      <svg viewBox="0 0 12 12"><circle cx="6" cy="6" r="5.5"/><path d="M0.5 6h11M6 0.5v11" stroke="#f4f4f3" stroke-width="1"/></svg>
      www.maraquillonconsulting.com
    </li>
  </ul>

  <div class="person">
    <div class="person__name">Mara Quillon</div>
    <div class="person__role">Owner</div>
  </div>

  <svg class="footer-band" viewBox="0 0 540 80" aria-hidden="true">
    <path d="M0 60 H250 V80 H0 Z" fill="var(--edge)"/>
    <path d="M244 26 Q244 12 258 12 H540 V80 H244 Z" fill="var(--charcoal)"/>
  </svg>
  <div class="footer-tab"><span class="footer-tab__label">Mara Quillon Consulting, LLC</span></div>
</section>

</body>
</html>
```